Federal Government Proposal Development Consulting company needs a website designed and coded

I am looking for someone to design (using an existing logo, color palette, and text fonts) and code a wordpress-based website for a Proposal Development consulting company. I have full copy for all site pages and suggestions for images/ graphics and a few example design templates to go from.

One note, from a color perspective - I included a mockup of a business card to highlight a color scheme that I tend to like - if you look at the back of the business card, the blend of the grey, blue, with the neon green highlight as a separator really seems to pop. Just a thought as you are designing the page.

I would like to see 2-3 potential design layouts, and I will select one to move forward with. Then, I would like the site to be coded for WordPress (I can provide a login to my wordpress site). I would like 1 opportunity to review the coded site and make any final tweaks.

```html
<!DOCTYPE html>
<html lang="en">
<head>
<meta charset="utf-8">
<title>The Bright Quill Consulting LLC</title>
<link rel="stylesheet" href="https://fonts.googleapis.com/css2?family=Cinzel:wght@500;600;700&family=Jost:wght@400;500;600&display=swap">
<style>
:root{
  --navy:#0a0a52;
  --navy-deep:#05053a;
  --blue:#1d2aa6;
  --mist:#efeff5;
  --line:#d5d6e4;
  --ink:#1b1b2e;
  --muted:#55566a;
  --white:#ffffff;
  --gold:#f2a81d;
}
*{box-sizing:border-box;margin:0;padding:0}
html,body{width:1200px;height:4804px;overflow:hidden}
body{font-family:"Jost",sans-serif;color:var(--ink);background:var(--white);position:relative}
.abs{position:absolute}
.serif{font-family:"Cinzel",serif}
.btn{position:absolute;display:flex;align-items:center;justify-content:center;gap:10px;background:var(--navy);color:var(--white);font-size:15px;font-weight:500;border-radius:6px}
.heading{position:absolute;display:flex;align-items:flex-end;gap:4px;font-family:"Cinzel",serif;font-size:34px;font-weight:600;color:var(--navy);line-height:1.1;white-space:nowrap}
.heading.centered{left:0;width:1200px;justify-content:center}
.heading .lead{font-size:42px}
.heading .light{font-weight:500}
.flourish{flex:none;width:86px;height:30px;margin-bottom:2px}
.flourish path{stroke:var(--navy);stroke-width:3;fill:none;stroke-linecap:round}
.heading.on-dark{color:var(--white)}
.heading.on-dark .flourish path{stroke:var(--white)}
.arrow-btn{position:absolute;width:36px;height:36px;border-radius:50%;background:var(--navy);display:flex;align-items:center;justify-content:center}

/* header */
.hero-photo{left:0;top:0;width:1200px;height:580px;background:linear-gradient(100deg,#f4f1ec 0%,#e7ddd0 35%,#c6a88a 62%,#8f735e 100%)}
.nav{left:0;top:0;width:1200px;height:80px}
.brand{position:absolute;left:108px;top:22px;font-size:24px;font-weight:500;color:var(--navy);line-height:1}
.brand small{display:block;font-size:12px;margin-top:4px;letter-spacing:1px}
.brand-footer{left:108px;top:4470px;color:var(--white)}
.nav-bar{position:absolute;left:455px;top:18px;width:645px;height:46px;background:var(--navy);border-radius:4px;display:flex;align-items:center;padding-left:28px;gap:40px;color:var(--white);font-size:16px}
.nav-bar .contact{margin-left:auto;margin-right:14px;background:var(--white);color:var(--navy);padding:7px 30px;border-radius:4px;font-weight:600}
.hero-title{left:108px;top:130px;font-size:52px;font-weight:700;color:var(--navy);white-space:nowrap}
.hero-title span{font-weight:500}
.hero-sub{left:108px;top:210px;width:430px;font-size:19px;line-height:1.4;color:var(--navy)}
.hero-band{left:0;top:440px}

/* what we do */
.intro{left:300px;top:796px;width:600px;text-align:center;font-size:15px;line-height:1.6;color:var(--muted)}
.card{position:absolute;top:874px;width:270px;height:290px;background:var(--white);box-shadow:0 6px 22px rgba(10,10,82,.14);text-align:center;padding:28px 32px}
.card.active{background:var(--navy);color:var(--white)}
.card h3{font-size:19px;font-weight:600;margin:20px 0 14px;color:var(--navy)}
.card.active h3{color:var(--white)}
.card p{font-size:15px;line-height:1.5}
.card-icon{width:48px;height:48px;margin:0 auto}

/* who we are */
.who-bg{left:0;top:1300px;width:1200px;height:660px;background:var(--mist)}
.who-text{left:108px;top:1462px;width:500px;font-size:15px;line-height:1.55;color:var(--muted)}
.stat{position:absolute;top:1776px}
.stat b{display:block;font-size:40px;font-weight:600;color:var(--navy);line-height:1}
.stat span{font-size:14px;color:var(--muted)}
.who-photo{left:672px;top:1420px;width:416px;height:440px;background:linear-gradient(135deg,#7fa0bd 0%,#4f6f8d 45%,#2f4156 100%)}

/* services */
.services-bg{left:0;top:1960px}
.svc-photo{left:108px;top:2132px;width:440px;height:336px;background:linear-gradient(135deg,#2d3fae 0%,#18196a 55%,#0a0a3a 100%);border-radius:2px}
.svc-list{left:600px;top:2172px;width:488px}
.svc-item{display:flex;align-items:center;gap:18px;height:44px;padding-left:14px;font-size:16px;font-weight:500;color:var(--navy);border-bottom:1px solid var(--line)}
.svc-item.active{background:linear-gradient(90deg,var(--navy),#3b4bd6);color:var(--white);border:none}
.svc-ico{width:22px;height:22px}

/* expertise */
.exp-item{position:absolute;top:2812px;width:256px;text-align:center}
.exp-circle{width:256px;height:256px;border-radius:50%;border-bottom:14px solid var(--blue);overflow:hidden}
.exp-fill{width:100%;height:100%}
.exp-badge{width:40px;height:40px;border-radius:50%;background:var(--navy);margin:-24px auto 0;position:relative;border:3px solid var(--white)}
.exp-item p{margin-top:18px;font-size:16px;font-weight:500;color:var(--navy);line-height:1.3}

/* contact */
.contact-bg{left:0;top:3280px;width:1200px;height:340px;background:var(--navy)}
.contact-col{position:absolute;top:3440px;width:300px;text-align:center;color:var(--white)}
.contact-col .ic{width:40px;height:40px;border-radius:50%;background:var(--white);margin:0 auto 14px;display:flex;align-items:center;justify-content:center}
.contact-col .lbl{font-size:14px;opacity:.9}
.contact-col .val{font-size:19px;margin-top:8px}
.form-card{left:208px;top:3592px;width:880px;height:350px;background:var(--white);box-shadow:0 8px 28px rgba(10,10,82,.16)}
.field{position:absolute;border:1px solid #c9cad8;border-radius:3px;font-size:15px;color:var(--muted);padding:14px 18px}

/* testimonials */
.quote-art{left:150px;top:4090px;width:140px;height:240px;background:linear-gradient(160deg,#3a49c8 0%,#141470 100%);opacity:.85}
.t-card{left:296px;top:4150px;width:660px;height:172px;background:var(--white);border:2px solid var(--navy);box-shadow:0 6px 20px rgba(10,10,82,.1)}
.t-text{left:390px;top:4172px;width:540px;font-size:15px;line-height:1.55;color:var(--muted)}
.t-avatar{left:310px;top:4248px;width:64px;height:64px;border-radius:50%;background:linear-gradient(135deg,#8c8fa8,#3a3c58)}
.t-name{left:390px;top:4270px;font-size:17px;font-weight:600;color:var(--navy)}

/* footer */
.footer{left:0;top:4380px;width:1200px;height:424px;background:var(--navy-deep)}
.foot-col{position:absolute;top:4470px;text-align:center;color:var(--white)}
.foot-col .ic{width:40px;height:40px;border-radius:50%;background:var(--white);margin:0 auto 16px;display:flex;align-items:center;justify-content:center}
.foot-col .lbl{font-size:15px}
.foot-col .val{font-size:15px;margin-top:6px}
.foot-nav{left:0;top:4694px;width:1200px;display:flex;justify-content:center;gap:40px;color:var(--white);font-size:15px}
.copyright{left:0;top:4740px;width:1200px;text-align:center;color:#c9cae0;font-size:13px}
</style>
</head>
<body>

<!-- HERO -->
<div class="abs hero-photo" role="img" aria-label="Consulting team reviewing proposal documents together at a bright office table"></div>
<header class="abs nav">
  <div class="brand">The Bright Quill<small>Consulting LLC</small></div>
  <nav class="nav-bar"><span>Home</span><span>Work with Us</span><span>Work for Us</span><span>About Us</span><span class="contact">Contact</span></nav>
</header>
<h1 class="abs hero-title serif">GENERATE <span>SUCCESS</span></h1>
<p class="abs hero-sub">Fuel Innovation in Proposal Excellence with The Bright Quill!</p>
<div class="btn" style="left:108px;top:364px;width:220px;height:42px">To Explore Our Services
  <svg width="16" height="10" viewBox="0 0 16 10"><path d="M0 5h14M10 1l4 4-4 4" stroke="#fff" stroke-width="1.8" fill="none"/></svg></div>
<svg class="abs hero-band" width="1200" height="160" viewBox="0 0 1200 160">
  <polygon points="0,40 600,140 1200,20 1200,160 0,160" fill="#fff"/>
  <polygon points="0,40 600,140 1200,20 1200,56 600,150 0,70" fill="#0a0a52"/>
  <polygon points="0,70 600,150 1200,56 1200,64 600,156 0,80" fill="#d8d9e8"/>
</svg>

<!-- WHAT WE DO -->
<h2 class="heading centered" style="top:722px"><span><span class="lead">W</span>HAT <span class="lead">W</span>E DO</span><svg class="flourish" viewBox="0 0 86 30"><path d="M2 27 C30 24 60 14 84 3"/></svg></h2>
<p class="abs intro">The Bright Quill specializes in advancing an organization through a comprehensive suite of services designed to modernize the proposal development process.</p>

<div class="card" style="left:116px">
  <svg class="card-icon" viewBox="0 0 48 48"><rect x="8" y="14" width="32" height="24" rx="3" fill="none" stroke="#1d2aa6" stroke-width="2.5"/><path d="M18 14v-5h12v5" fill="none" stroke="#1d2aa6" stroke-width="2.5"/></svg>
  <h3>Capture Management</h3>
  <p>Elevate your business development strategy with our Capture Management</p>
</div>
<div class="card active" style="left:465px">
  <svg class="card-icon" viewBox="0 0 48 48"><path d="M6 40 L18 24 L26 32 L42 10" fill="none" stroke="#fff" stroke-width="2.5"/><path d="M34 10h8v8" fill="none" stroke="#fff" stroke-width="2.5"/></svg>
  <h3>Proposal Development</h3>
  <p>Transform your vision into winning proposals with our Proposal Development</p>
</div>
<div class="card" style="left:814px">
  <svg class="card-icon" viewBox="0 0 48 48"><rect x="12" y="12" width="24" height="24" rx="3" fill="none" stroke="#1d2aa6" stroke-width="2.5"/><path d="M18 4v8M30 4v8M18 36v8M30 36v8M4 18h8M4 30h8M36 18h8M36 30h8" stroke="#1d2aa6" stroke-width="2.5"/></svg>
  <h3>Generative AI</h3>
  <p>Revolutionize your proposal writing process with our domain-aware Generative AI</p>
</div>
<div class="btn" style="left:530px;top:1176px;width:140px;height:40px">View More
  <svg width="16" height="10" viewBox="0 0 16 10"><path d="M0 5h14M10 1l4 4-4 4" stroke="#fff" stroke-width="1.8" fill="none"/></svg></div>

<!-- WHO WE ARE -->
<div class="abs who-bg"></div>
<h2 class="heading" style="left:108px;top:1386px"><span><span class="lead">W</span>HO <span class="lead">W</span>E ARE</span><svg class="flourish" viewBox="0 0 86 30"><path d="M2 27 C30 24 60 14 84 3"/></svg></h2>
<p class="abs who-text">Lorem ipsum dolor sit amet, consectetur adipiscing elit, sed do eiusmod tempor incididunt ut labore et dolore magna aliqua. Ut enim ad minim veniam, quis nostrud exercitation ullamco laboris nisi ut aliquip ex ea commodo consequat. Duis aute irure dolor in reprehenderit in voluptate velit esse cillum dolore eu fugiat nulla pariatur. Excepteur sint occaecat cupidatat non proident, sunt in culpa qui officia deserunt mollit anim id est laborum.</p>
<div class="btn" style="left:108px;top:1648px;width:130px;height:38px">About Us
  <svg width="16" height="10" viewBox="0 0 16 10"><path d="M0 5h14M10 1l4 4-4 4" stroke="#fff" stroke-width="1.8" fill="none"/></svg></div>
<svg class="abs" style="left:108px;top:1734px" width="32" height="28" viewBox="0 0 32 28"><circle cx="16" cy="8" r="6" fill="#0a0a52"/><path d="M4 28c0-8 6-12 12-12s12 4 12 12z" fill="#0a0a52"/></svg>
<svg class="abs" style="left:256px;top:1734px" width="32" height="28" viewBox="0 0 32 28"><circle cx="16" cy="8" r="6" fill="#0a0a52"/><path d="M4 28c0-8 6-12 12-12s12 4 12 12z" fill="#0a0a52"/></svg>
<svg class="abs" style="left:396px;top:1734px" width="32" height="28" viewBox="0 0 32 28"><rect x="4" y="16" width="6" height="12" fill="#0a0a52"/><rect x="13" y="8" width="6" height="20" fill="#0a0a52"/><rect x="22" y="2" width="6" height="26" fill="#0a0a52"/></svg>
<div class="stat" style="left:108px"><b>1000+</b><span>Happy Clients</span></div>
<div class="stat" style="left:256px"><b>150+</b><span>Experts On Staff</span></div>
<div class="stat" style="left:396px"><b>$100</b><span>Billion in Contracts Won</span></div>
<div class="abs who-photo" role="img" aria-label="Two consultants reviewing a proposal on a laptop"></div>

<!-- SERVICES -->
<svg class="abs services-bg" width="1200" height="700" viewBox="0 0 1200 700">
  <polygon points="0,80 600,10 1200,80 1200,660 600,600 0,660" fill="#efeff5"/>
  <polygon points="0,50 600,0 1200,50 1200,80 600,10 0,80" fill="#0a0a52"/>
  <polygon points="0,660 600,600 1200,660 1200,700 0,700" fill="#0a0a52"/>
</svg>
<h2 class="heading centered" style="top:2072px"><span><span class="lead">O</span>UR <span class="lead">S</span>ERVICES</span><svg class="flourish" viewBox="0 0 86 30"><path d="M2 27 C30 24 60 14 84 3"/></svg></h2>
<div class="abs svc-photo" role="img" aria-label="Digital interface with artificial intelligence dashboards"></div>
<div class="btn" style="left:258px;top:2410px;width:130px;height:36px">View More
  <svg width="16" height="10" viewBox="0 0 16 10"><path d="M0 5h14M10 1l4 4-4 4" stroke="#fff" stroke-width="1.8" fill="none"/></svg></div>
<div class="arrow-btn" style="left:1008px;top:2128px"><svg width="10" height="14" viewBox="0 0 10 14"><path d="M8 1L2 7l6 6" stroke="#fff" stroke-width="2" fill="none"/></svg></div>
<div class="arrow-btn" style="left:1052px;top:2128px"><svg width="10" height="14" viewBox="0 0 10 14"><path d="M2 1l6 6-6 6" stroke="#fff" stroke-width="2" fill="none"/></svg></div>
<div class="abs svc-list">
  <div class="svc-item active"><svg class="svc-ico" viewBox="0 0 22 22"><rect x="5" y="5" width="12" height="12" fill="none" stroke="#fff" stroke-width="2"/></svg>Generative AI</div>
  <div class="svc-item"><svg class="svc-ico" viewBox="0 0 22 22"><circle cx="11" cy="11" r="7" fill="none" stroke="#0a0a52" stroke-width="2"/><circle cx="11" cy="11" r="2" fill="#0a0a52"/></svg>Technical Solutioning</div>
  <div class="svc-item"><svg class="svc-ico" viewBox="0 0 22 22"><path d="M3 19L9 11l4 4 6-10" fill="none" stroke="#0a0a52" stroke-width="2"/></svg>Price to Win/ Competitive Intelligence</div>
  <div class="svc-item"><svg class="svc-ico" viewBox="0 0 22 22"><circle cx="11" cy="11" r="8" fill="none" stroke="#0a0a52" stroke-width="2"/><path d="M11 6v5l3 3" stroke="#0a0a52" stroke-width="2" fill="none"/></svg>Capture Management</div>
  <div class="svc-item"><svg class="svc-ico" viewBox="0 0 22 22"><rect x="4" y="3" width="14" height="16" rx="2" fill="none" stroke="#0a0a52" stroke-width="2"/><path d="M8 8h6M8 12h6" stroke="#0a0a52" stroke-width="2"/></svg>Proposal Management</div>
  <div class="svc-item"><svg class="svc-ico" viewBox="0 0 22 22"><circle cx="11" cy="11" r="8" fill="none" stroke="#0a0a52" stroke-width="2"/><path d="M7 11l3 3 5-6" stroke="#0a0a52" stroke-width="2" fill="none"/></svg>Compliance Reviews</div>
</div>

<!-- SUBJECT MATTER EXPERTISE -->
<h2 class="heading" style="left:108px;top:2716px;font-size:32px"><span><span class="lead" style="font-size:40px">S</span>UBJECT <span class="light"><span class="lead" style="font-size:40px">M</span>ATTER <span class="lead" style="font-size:40px">E</span>XPERTISE</span></span><svg class="flourish" viewBox="0 0 86 30"><path d="M2 27 C30 24 60 14 84 3"/></svg></h2>
<div class="arrow-btn" style="left:1008px;top:2722px"><svg width="10" height="14" viewBox="0 0 10 14"><path d="M8 1L2 7l6 6" stroke="#fff" stroke-width="2" fill="none"/></svg></div>
<div class="arrow-btn" style="left:1052px;top:2722px"><svg width="10" height="14" viewBox="0 0 10 14"><path d="M2 1l6 6-6 6" stroke="#fff" stroke-width="2" fill="none"/></svg></div>
<div class="exp-item" style="left:124px">
  <div class="exp-circle"><div class="exp-fill" role="img" aria-label="Humanoid robot representing generative AI" style="background:linear-gradient(135deg,#d6d9e2,#6f7689)"></div></div>
  <div class="exp-badge"></div><p>Generative AI,</p></div>
<div class="exp-item" style="left:472px">
  <div class="exp-circle"><div class="exp-fill" role="img" aria-label="Engineer working at a computer workstation" style="background:linear-gradient(135deg,#3c5a86,#0f1c3a)"></div></div>
  <div class="exp-badge"></div><p>Software/ Hardware<br>Engineering</p></div>
<div class="exp-item" style="left:820px">
  <div class="exp-circle"><div class="exp-fill" role="img" aria-label="Team of systems engineers in a meeting" style="background:linear-gradient(135deg,#a9b7c9,#4a5a72)"></div></div>
  <div class="exp-badge"></div><p>Systems Engineering</p></div>

<!-- CONTACT -->
<div class="abs contact-bg"></div>
<h2 class="heading centered on-dark" style="top:3352px"><span><span class="lead">C</span>ONTACT <span class="lead">U</span>S</span><svg class="flourish" viewBox="0 0 86 30"><path d="M2 27 C30 24 60 14 84 3"/></svg></h2>
<div class="contact-col" style="left:94px">
  <div class="ic"><svg width="18" height="18" viewBox="0 0 18 18"><path d="M4 1l3 4-2 2c1 2 3 4 5 5l2-2 4 3-2 3C8 16 2 10 1 4z" fill="#0a0a52"/></svg></div>
  <div class="lbl">Call Us</div><div class="val">(555) 014-2837</div></div>
<div class="contact-col" style="left:450px">
  <div class="ic"><svg width="18" height="14" viewBox="0 0 18 14"><rect x="1" y="1" width="16" height="12" fill="none" stroke="#0a0a52" stroke-width="2"/><path d="M1 1l8 7 8-7" fill="none" stroke="#0a0a52" stroke-width="2"/></svg></div>
  <div class="lbl">Email Address</div><div class="val">info@brightquill.example</div></div>
<div class="contact-col" style="left:806px">
  <div class="ic"><svg width="14" height="18" viewBox="0 0 14 18"><path d="M7 17C3 11 1 8 1 6a6 6 0 0112 0c0 2-2 5-6 11z" fill="#0a0a52"/><circle cx="7" cy="6" r="2" fill="#fff"/></svg></div>
  <div class="lbl">Location</div><div class="val" style="text-decoration:underline">View Map</div></div>
<div class="abs form-card"></div>
<div class="field" style="left:240px;top:3646px;width:360px;height:50px">Name</div>
<div class="field" style="left:612px;top:3646px;width:340px;height:50px">Email</div>
<div class="field" style="left:240px;top:3720px;width:712px;height:104px">Message</div>
<div class="btn" style="left:530px;top:3852px;width:140px;height:40px">Submit</div>

<!-- TESTIMONIALS -->
<h2 class="heading centered" style="top:3998px"><span><span class="lead">O</span>UR <span class="lead">T</span>ESTIMONIALS</span><svg class="flourish" viewBox="0 0 86 30"><path d="M2 27 C30 24 60 14 84 3"/></svg></h2>
<div class="arrow-btn" style="left:108px;top:4196px"><svg width="10" height="14" viewBox="0 0 10 14"><path d="M8 1L2 7l6 6" stroke="#fff" stroke-width="2" fill="none"/></svg></div>
<div class="arrow-btn" style="left:1052px;top:4196px"><svg width="10" height="14" viewBox="0 0 10 14"><path d="M2 1l6 6-6 6" stroke="#fff" stroke-width="2" fill="none"/></svg></div>
<div class="abs quote-art" role="img" aria-label="Quill feather beside an ink stroke"></div>
<div class="abs t-card"></div>
<p class="abs t-text">Lorem ipsum dolor sit amet, consectetur adipiscing elit, sed do eiusmod tempor incididunt ut labore et dolore magna aliqua. Ut enim ad minim veniam, quis nostrud exercitation ullamco laboris nisi ut aliquip ex ea.</p>
<div class="abs t-avatar" role="img" aria-label="Client portrait"></div>
<div class="abs t-name">Dana Reyes</div>
<svg class="abs" style="left:496px;top:4274px" width="100" height="18" viewBox="0 0 100 18">
  <g fill="#f2a81d">
    <path id="st" d="M9 1l2.4 5 5.4.6-4 3.7 1.1 5.3L9 13l-4.9 2.6 1.1-5.3-4-3.7 5.4-.6z"/>
    <use href="#st" x="20"/><use href="#st" x="40"/><use href="#st" x="60"/><use href="#st" x="80"/>
  </g>
</svg>
<div class="abs" style="left:812px;top:4276px;font-size:14px;color:var(--muted);text-decoration:underline">View More</div>

<!-- FOOTER -->
<footer class="abs footer"></footer>
<div class="brand brand-footer">The Bright Quill<small>Consulting LLC</small></div>
<div class="foot-col" style="left:540px;width:120px">
  <div class="ic"><svg width="18" height="18" viewBox="0 0 18 18"><path d="M4 1l3 4-2 2c1 2 3 4 5 5l2-2 4 3-2 3C8 16 2 10 1 4z" fill="#05053a"/></svg></div>
  <div class="lbl">Call Us</div><div class="val">(555) 014-2837</div></div>
<div class="foot-col" style="left:900px;width:200px">
  <div class="ic"><svg width="18" height="14" viewBox="0 0 18 14"><rect x="1" y="1" width="16" height="12" fill="none" stroke="#05053a" stroke-width="2"/><path d="M1 1l8 7 8-7" fill="none" stroke="#05053a" stroke-width="2"/></svg></div>
  <div class="lbl">Email Address</div><div class="val">info@brightquill.example</div></div>
<nav class="abs foot-nav"><span>Home</span><span>Work with Us</span><span>Work for Us</span><span>About Us</span></nav>
<p class="abs copyright">Copyright © 2024 - All Rights Reserved By The Bright Quill Consulting LLC</p>

</body>
</html>
```